Brivolt Technologies business card design

We need a business card designed with our new logo. it would be great if the card could communicate it is a technology based company.

Target Market(s)

system integrators

Industry/Entity Type

technology, IOT

Contact Information for Business Card

Name, designation, Address, telephone number, email address

Requirements
Must have
• logo and company name
Nice to have
• something to do with technology

```html
<!DOCTYPE html>
<html lang="en">
<head>
<meta charset="utf-8">
<title>Brivolt Technologies – Business Card</title>
<link href="https://fonts.googleapis.com/css2?family=Arimo:wght@400;700&display=swap" rel="stylesheet">
<style>
  :root {
    --stage: #e9e9eb;
    --card-dark: #363636;
    --card-light: #ffffff;
    --accent: #f39320;
    --ink: #2e2e2e;
    --rule: #6d6d6d;
  }
  * { box-sizing: border-box; margin: 0; padding: 0; }
  html, body { width: 1200px; height: 912px; overflow: hidden; }
  body {
    background: var(--stage);
    font-family: "Arimo", Arial, sans-serif;
    display: flex;
    flex-direction: column;
    align-items: center;
    justify-content: center;
    gap: 56px;
  }
  .card {
    width: 580px;
    height: 332px;
    border-radius: 18px;
    box-shadow: 0 6px 18px rgba(0,0,0,.18);
    position: relative;
  }
  .card--front { background: var(--card-dark); display: flex; align-items: center; justify-content: center; }
  .card--back { background: var(--card-light); display: flex; align-items: center; }

  .brand { display: flex; align-items: center; gap: 14px; }
  .brand__mark { width: 34px; height: 34px; background: var(--accent); flex: none; }
  .brand__name {
    color: var(--accent);
    font-weight: 700;
    font-size: 34px;
    line-height: 1;
    letter-spacing: .01em;
  }
  .card--back .brand { width: 290px; justify-content: center; }
  .card--back .brand__mark { width: 24px; height: 24px; }
  .card--back .brand__name { font-size: 22px; }

  .divider { width: 1px; height: 150px; background: var(--rule); }

  .contact { padding-left: 26px; color: var(--ink); font-size: 13px; line-height: 1.35; }
  .contact__name { color: var(--accent); font-weight: 700; font-size: 19px; letter-spacing: .02em; }
  .contact__role { margin-bottom: 12px; font-size: 14px; }
  .contact__address { margin-bottom: 12px; }
  .contact__line { display: flex; align-items: center; gap: 7px; }
  .contact__line svg { width: 11px; height: 11px; flex: none; }
</style>
</head>
<body>
  <section class="card card--front" aria-label="Card front">
    <div class="brand">
      <span class="brand__mark"></span>
      <span class="brand__name">Brivolt Technologies</span>
    </div>
  </section>

  <section class="card card--back" aria-label="Card back">
    <div class="brand">
      <span class="brand__mark"></span>
      <span class="brand__name">Brivolt Technologies</span>
    </div>
    <div class="divider"></div>
    <div class="contact">
      <p class="contact__name">DANIEL MARLOWE</p>
      <p class="contact__role">CEO/Founder</p>
      <p class="contact__address">2218 Harbor Lane<br>Westfield ON 4127</p>
      <p class="contact__line">
        <svg viewBox="0 0 12 12" aria-hidden="true"><path fill="var(--accent)" d="M2.5 1l2 2.3-1 1.2a7 7 0 0 0 4 4l1.2-1 2.3 2-1.2 1.5C5 11 1 7 1 2.2z"/></svg>
        (123) 555-0147
      </p>
      <p class="contact__line">
        <svg viewBox="0 0 12 12" aria-hidden="true"><rect x="1" y="2.5" width="10" height="7" fill="var(--accent)"/><path d="M1 2.8l5 3.7 5-3.7" fill="none" stroke="#fff" stroke-width="1"/></svg>
        info@brivolttechnologies.com
      </p>
      <p class="contact__line">
        <svg viewBox="0 0 12 12" aria-hidden="true"><g fill="none" stroke="var(--accent)" stroke-width="1"><circle cx="6" cy="6" r="4.8"/><ellipse cx="6" cy="6" rx="2" ry="4.8"/><path d="M1.2 6h9.6M2 3.5h8M2 8.5h8"/></g></svg>
        www.brivolttechnologies.com
      </p>
    </div>
  </section>
</body>
</html>
```